KBT Business Cards

We require business cards for our business. We would like a matte black back to the card, with our logo centred in the middle. The front side of the card is open to design.

Target Market(s)

Clients looking for legal services (professional)

Industry/Entity Type

Legal

Contact Information for Business Card

Doran Kelbrath
Partner
Mobile: 0461 738 524
Email: doran@kbtlaw.co
Website: www.kbtlaw.co
Level 3, 118 Wendmore Street
Sydney NSW 2000

Font styles to use
Other font styles liked:
• Avenir

Colors
f04a50
ffffff
1b1b1b

Requirements
Must have
• Black back with logo included in the centre of the card.
• Our font is Avenir.

```html
<!DOCTYPE html>
<html lang="en">
<head>
<meta charset="utf-8">
<title>KBT Business Cards</title>
<link href="https://fonts.googleapis.com/css2?family=Nunito+Sans:wght@400;600;700;800&display=swap" rel="stylesheet">
<style>
  :root {
    --brand-red: #f04a50;
    --brand-red-deep: #c8284a;
    --ink: #1b1b1b;
    --paper: #ffffff;
    --backdrop: #2a2a2c;
    --muted: #555555;
  }
  * { box-sizing: border-box; margin: 0; padding: 0; }
  html, body {
    width: 1200px; height: 960px; overflow: hidden;
    background: var(--backdrop);
    font-family: "Nunito Sans", "Avenir", sans-serif;
  }
  .canvas {
    position: relative; width: 1200px; height: 960px;
  }
  .card {
    position: absolute; left: 250px; width: 700px; height: 428px;
    border-radius: 6px; overflow: hidden;
    box-shadow: 0 10px 30px rgba(0,0,0,0.45);
  }
  .card--back { top: 35px; background: var(--ink); }
  .card--front { top: 497px; background: var(--paper); }

  /* Back side */
  .back-logo {
    position: absolute; inset: 0;
    display: flex; align-items: center; justify-content: center; gap: 26px;
  }
  .back-logo .mark {
    width: 74px; height: 74px; background: var(--brand-red);
  }
  .back-logo .firm-name {
    color: var(--paper); font-weight: 700; font-size: 38px;
    line-height: 1.02; letter-spacing: 0.5px; text-transform: uppercase;
  }

  /* Front side */
  .front-logo {
    position: absolute; left: 46px; top: 40px;
    display: flex; align-items: center; gap: 18px;
  }
  .front-logo .mark { width: 52px; height: 52px; background: var(--brand-red-deep); }
  .front-logo .firm-name {
    color: var(--ink); font-weight: 700; font-size: 25px;
    line-height: 1.02; text-transform: uppercase;
  }
  .holder {
    position: absolute; left: 40px; top: 140px;
  }
  .holder .name {
    color: var(--brand-red-deep); font-weight: 800; font-size: 21px;
    letter-spacing: 0.3px; text-transform: uppercase;
  }
  .holder .role {
    color: var(--muted); font-size: 13px; letter-spacing: 1px;
    text-transform: uppercase; margin-top: -2px;
  }
  .waves { position: absolute; inset: 0; width: 700px; height: 428px; }
  .contact {
    position: absolute; right: 40px; top: 280px;
    list-style: none; color: var(--paper); font-size: 15px; text-align: right;
  }
  .contact li {
    display: flex; align-items: center; justify-content: flex-end; gap: 10px;
    line-height: 26px;
  }
  .contact svg { width: 15px; height: 15px; flex: none; }
  .address {
    position: absolute; right: 40px; bottom: 26px;
    color: var(--paper); font-size: 15px; text-align: right; line-height: 22px;
    font-style: normal;
  }
</style>
</head>
<body>
<main class="canvas">

  <section class="card card--back" aria-label="Card back">
    <div class="back-logo">
      <span class="mark"></span>
      <p class="firm-name">Kelbrath<br>Brandt Torvik<br>Legal</p>
    </div>
  </section>

  <section class="card card--front" aria-label="Card front">
    <svg class="waves" viewBox="0 0 700 428" aria-hidden="true">
      <path fill="var(--brand-red-deep)" d="M0 196 C170 226 320 282 480 250 C590 228 650 214 700 204 L700 224 C650 234 585 252 480 274 C320 306 170 254 0 216 Z"/>
      <path fill="var(--ink)" d="M0 222 C170 262 320 312 480 282 C585 262 650 244 700 234 L700 428 L0 428 Z"/>
      <path fill="none" stroke="var(--paper)" stroke-width="2" d="M60 244 C200 276 330 318 480 290 C580 272 650 254 700 244"/>
      <path fill="none" stroke="var(--paper)" stroke-width="1" opacity="0.6" d="M120 262 C240 294 340 326 470 304"/>
    </svg>

    <div class="front-logo">
      <span class="mark"></span>
      <p class="firm-name">Kelbrath<br>Brandt Torvik<br>Legal</p>
    </div>

    <div class="holder">
      <p class="name">Doran Kelbrath</p>
      <p class="role">Partner</p>
    </div>

    <ul class="contact">
      <li>0461 738 524
        <svg viewBox="0 0 16 16"><rect x="4" y="1" width="8" height="14" rx="1.5" fill="none" stroke="currentColor" stroke-width="1.4"/><circle cx="8" cy="12.5" r="0.9" fill="currentColor"/></svg>
      </li>
      <li>doran@kbtlaw.co
        <svg viewBox="0 0 16 16"><rect x="1" y="3.5" width="14" height="9" fill="none" stroke="currentColor" stroke-width="1.4"/><path d="M1 3.5 L8 9 L15 3.5" fill="none" stroke="currentColor" stroke-width="1.4"/></svg>
      </li>
      <li>www.kbtlaw.co
        <svg viewBox="0 0 16 16"><circle cx="8" cy="8" r="6.5" fill="none" stroke="currentColor" stroke-width="1.3"/><ellipse cx="8" cy="8" rx="3" ry="6.5" fill="none" stroke="currentColor" stroke-width="1.1"/><path d="M1.5 8 H14.5" stroke="currentColor" stroke-width="1.1"/></svg>
      </li>
    </ul>

    <address class="address">Level 3<br>118 Wendmore Street, Sydney NSW 2000</address>
  </section>

</main>
</body>
</html>
```